Trade Show booth design

I need the following designs for my trade booth:
1. backboard design 3m Wx2mH
2. Tressle table, tablecloth front panel design 1800W x 740mmH
3. Pop-up banner. I have included our logos and some design content ideas:
Headline:
"Cleaner Classrooms. Safer Schools."
Subheadline:
"Specialist Cleaning Solutions for Education Facilities"
Key Points to Grab Attention:
Healthy Environments: Create hygienic, safe learning spaces for students and staff with our expert cleaning services.
Tailored to Your Needs: Custom cleaning plans for classrooms, labs, libraries, and sports facilities.
Affordable Excellence: Premium results without premium costs – tailored plans mean you only pay for what you need.
Safety First: All staff are trained, highly vetted, and hold current Working with Children Checks (WWCC).
Eco-Conscious Cleaning: Using non-toxic, eco-friendly products certified for health and safety.
What Schools Really Need:
Reliability: Consistent, high-quality cleaning from a trusted provider.
Cost-Effectiveness: Solutions that fit tight budgets while maintaining high standards.
Expertise: Over 30 years of experience in education facility cleaning.
Disinfection Services: Focus on high-touch areas to reduce the spread of germs and ensure peace of mind.
Visual Elements:
Images of bright, clean classrooms, a happy teacher welcoming students, or students collaborating in a spotless library.
Icons representing safety (shield), hygiene (sparkling star), and eco-friendliness (leaf).
Your logo with the tagline: "Trusted by Queensland Schools Since 1995."
Call-to-Action:
"Visit us to discuss your school’s cleaning needs and book a FREE consultation."
Include contact details: Phone: 1300 594 316 | Website: www.brightmorefacility.com.au
Target Market(s)
Education sector
Industry/Entity Type
Commercial Cleaning
Font styles to use
Other font styles liked:
- Montserrat
Look and feel

```html
<!DOCTYPE html>
<html lang="en">
<head>
<meta charset="utf-8">
<title>Brightmore Facility Cleaning – Banner</title>
<link rel="stylesheet" href="https://fonts.googleapis.com/css2?family=Montserrat:wght@500;600&family=Raleway:wght@400&display=swap">
<style>
  :root {
    --stage: #bebebe;
    --navy: #1e3f62;
    --navy-deep: #1a3757;
    --navy-light: #2a5582;
    --white: #ffffff;
    --ink: #161616;
    --accent: #1a8bb5;
  }
  * { box-sizing: border-box; margin: 0; padding: 0; }
  html, body {
    width: 1200px;
    height: 850px;
    overflow: hidden;
    background: var(--stage);
  }
  .banner {
    position: absolute;
    left: 0;
    top: 179px;
    width: 1200px;
    height: 492px;
    background: var(--navy);
    overflow: hidden;
  }
  .banner__backdrop {
    position: absolute;
    inset: 0;
    background:
      radial-gradient(ellipse 40% 60% at 45% 45%, var(--navy-light) 0%, transparent 70%),
      linear-gradient(90deg, var(--navy-deep) 0%, var(--navy) 40%, var(--navy) 70%, var(--navy-deep) 100%);
  }
  .brand {
    position: absolute;
    top: 142px;
    left: 0;
    width: 1200px;
    height: 135px;
  }
  .brand__dot {
    position: absolute;
    left: 510px;
    top: 20px;
    width: 96px;
    height: 96px;
    border-radius: 50%;
    background: var(--white);
  }
  .brand__divider {
    position: absolute;
    left: 637px;
    top: 0;
    width: 1.5px;
    height: 135px;
    background: var(--white);
  }
  .brand__name {
    position: absolute;
    left: 663px;
    top: 19px;
    font-family: "Raleway", sans-serif;
    font-weight: 400;
    font-size: 25px;
    line-height: 32px;
    color: var(--white);
    text-transform: uppercase;
    letter-spacing: 0.01em;
  }
  .url-band {
    position: absolute;
    left: 0;
    top: 326px;
    width: 1200px;
    height: 84px;
    background: var(--white);
    display: flex;
    align-items: center;
    justify-content: center;
  }
  .url-band__text {
    font-family: "Montserrat", sans-serif;
    font-weight: 600;
    font-size: 33px;
    letter-spacing: 0.2em;
    color: var(--ink);
    padding-left: 0.2em;
  }
  .url-band__domain { color: var(--accent); }
</style>
</head>
<body>
  <section class="banner">
    <div class="banner__backdrop" role="img" aria-label="Photo of a clean school corridor with lockers and classroom doors, tinted deep blue"></div>

    <div class="brand">
      <span class="brand__dot"></span>
      <span class="brand__divider"></span>
      <p class="brand__name">Brightmore<br>Facility<br>Cleaning</p>
    </div>

    <div class="url-band">
      <p class="url-band__text">www.<span class="url-band__domain">brightmorefacility</span>.com.au</p>
    </div>
  </section>
</body>
</html>
```